Upscale business cards needed for Board of Directors

We need professional business cards created for members of our family business Board of Directors. We would like these relatively simple and straightforward, but also with a unique element to set them apart. Probably stick with neutral and simple colors - white, grey etc. We need space for the traditional elements, including name, title, address, email/phone number. And we will be creating several from this template so it needs to be template that is easy to switch information in and out of.
Business
See description

```html
<!DOCTYPE html>
<html lang="en">
<head>
<meta charset="utf-8">
<title>Corvane Holdings – Business Cards</title>
<link href="https://fonts.googleapis.com/css2?family=Lato:wght@400;900&display=swap" rel="stylesheet">
<style>
  :root {
    --ink: #000000;
    --paper: #ffffff;
    --gold: #b8a47a;
    --stage: #3a3a3a;
    --muted: #e8e8e8;
  }
  * { margin: 0; padding: 0; box-sizing: border-box; }
  html, body { width: 1200px; height: 900px; overflow: hidden; }
  body {
    background: var(--stage);
    font-family: "Lato", sans-serif;
    position: relative;
  }
  .card {
    position: absolute;
    left: 300px;
    width: 600px;
    height: 343px;
    overflow: hidden;
    box-shadow: 0 6px 18px rgba(0,0,0,.45);
  }
  .card--back { top: 64px; background: var(--ink); }
  .card--front { top: 470px; background: var(--ink); }

  .wordmark {
    position: absolute;
    text-align: center;
    font-weight: 900;
    line-height: 1;
  }
  .wordmark__name { display: block; font-size: 52px; letter-spacing: 1px; }
  .wordmark__sub { display: block; font-size: 24px; letter-spacing: 14px; margin-top: 6px; padding-left: 14px; }

  .card--back .wordmark { left: 0; right: 0; top: 102px; color: var(--paper); }
  .card--back .site {
    position: absolute; left: 0; right: 0; top: 262px;
    text-align: center; color: var(--paper);
    font-size: 15px; letter-spacing: 2px;
  }

  .front-shape { position: absolute; inset: 0; width: 600px; height: 343px; }
  .card--front .wordmark { left: 300px; right: 0; top: 120px; color: var(--ink); }
  .card--front .wordmark__name { font-size: 42px; }
  .card--front .wordmark__sub { font-size: 19px; letter-spacing: 11px; padding-left: 11px; }

  .contact { position: absolute; left: 34px; top: 34px; color: var(--paper); }
  .contact__name { font-size: 23px; }
  .contact__title { font-size: 15px; color: var(--gold); margin-top: 2px; }
  .contact__address { font-size: 15px; line-height: 1.3; margin-top: 20px; }
  .contact__list { list-style: none; margin-top: 16px; font-size: 15px; line-height: 1.45; }
  .contact__list li { display: flex; align-items: center; gap: 10px; }
  .contact__list svg { width: 13px; height: 13px; fill: var(--gold); flex: none; }
</style>
</head>
<body>

<section class="card card--back" aria-label="Card back">
  <div class="wordmark">
    <span class="wordmark__name">CORVANE</span>
    <span class="wordmark__sub">HOLDINGS</span>
  </div>
  <p class="site">www.corvane.com</p>
</section>

<section class="card card--front" aria-label="Card front">
  <svg class="front-shape" viewBox="0 0 600 343" aria-hidden="true">
    <path d="M338 0 C262 70 232 200 262 343 L600 343 L600 0 Z" fill="var(--gold)"/>
    <path d="M360 0 C282 70 254 200 282 343 L600 343 L600 0 Z" fill="var(--ink)"/>
    <path d="M372 0 C296 70 268 200 296 343 L600 343 L600 0 Z" fill="var(--paper)"/>
  </svg>

  <div class="wordmark">
    <span class="wordmark__name">CORVANE</span>
    <span class="wordmark__sub">HOLDINGS</span>
  </div>

  <div class="contact">
    <p class="contact__name">Daniel Mercer</p>
    <p class="contact__title">Director</p>
    <p class="contact__address">1480 Elm Ridge Dr<br>Marlow TX 75000</p>
    <ul class="contact__list">
      <li>
        <svg viewBox="0 0 16 16"><path d="M3 1h3l1.5 4-2 1.5a9 9 0 0 0 4 4L11 8.5l4 1.5v3a2 2 0 0 1-2 2A12 12 0 0 1 1 3a2 2 0 0 1 2-2z"/></svg>
        555 014 2200
      </li>
      <li>
        <svg viewBox="0 0 16 16"><path d="M4 1h8v4H4zM1 6h14v7h-3v2H4v-2H1zM5 10v4h6v-4z"/></svg>
        555 014 2201
      </li>
      <li>
        <svg viewBox="0 0 16 16"><path d="M1 3h14v10H1zM2.5 4.5 8 9l5.5-4.5v-.2H2.5z"/></svg>
        info@corvane.com
      </li>
      <li>
        <svg viewBox="0 0 16 16"><path d="M8 1a7 7 0 1 0 0 14A7 7 0 0 0 8 1zm0 1.5c.9 0 1.9 2 2.1 4.7H5.9C6.1 4.5 7.1 2.5 8 2.5zM2.6 7.2h1.9a12 12 0 0 1 .9-4 5.5 5.5 0 0 0-2.8 4zm8.9 0h1.9a5.5 5.5 0 0 0-2.8-4 12 12 0 0 1 .9 4zM2.6 8.8a5.5 5.5 0 0 0 2.8 4 12 12 0 0 1-.9-4zm3.3 0c.2 2.7 1.2 4.7 2.1 4.7s1.9-2 2.1-4.7zm5.6 0a12 12 0 0 1-.9 4 5.5 5.5 0 0 0 2.8-4z"/></svg>
        www.corvane.com
      </li>
    </ul>
  </div>
</section>

</body>
</html>
```